VORLE Diagnostics Pooling One Sheet

The process and concept for pooling is to target large populations of people; i.e. a school, prison, employer (where people are isolated by pods), then to test them all in one controllable group. By breaking down the pool size (ideally is 12 or 16 max) then when a positive pool pops up, the entity has the lab automatically reflex to test the whole pool to determine who is positive. During that exchange, several workflows could take place from the population that was being tested. This type of pooled testing is called Surveillance testing ,when it reflects, then it goes to Screening or Diagnostic testing.

The workflow is:
School/employer collects all patient information captured on a requisition form or electronically (w signature) and DOES NOT send to VORLE
School/employer collects individual specimens and labels them with a unique bar code (non-repeating and can include the DOB)
School/employer is responsible for housing and managing all the unique patient information for each individual specimen
School/employer delivers specimens to VORLE and School/employer directs VORLE what specimens are in what designated pool (one pool size for entire project)
When a pool is positive, VORLE notifies School/employer
When reflex testing in indicated for client, School/employer submits to VORLE on demand all patient information needed to process the reflexed option
VORLE reports back to School/employer in 12 hours the results of the retest
https://www.healthregistry-example.org/medical-devices/coronavirus-covid-19-and-medical-devices/pooled-sample-testing-and-screening-testing-covid-19
https://www.testmere.com/coronavirus-disease-covid-19/news/testmere-receives-authorization-covid-19-sample-pooling

Target Market(s)

Schools, Universities, Employers

Font styles to use
Sans Serif

Colors
85acd3
85cae6
34a6d7

Requirements
Must have
• VORLE branded along with an elegant yet clinical feel. have all contact information for VORLE Diagnostics. Go to www.vorledx.com for all info

```html
<!DOCTYPE html>
<html lang="en">
<head>
<meta charset="utf-8">
<title>VORLE Diagnostics – Pooled Testing</title>
<link rel="stylesheet" href="https://fonts.googleapis.com/css2?family=Montserrat:wght@400;500;600;700;800&display=swap">
<style>
  :root {
    --teal: #2e9fb8;
    --teal-light: #34a6d7;
    --teal-dark: #1f5d6e;
    --navy: #2b4352;
    --ink: #2a2f33;
    --paper: #ffffff;
    --rule: #c9d3d8;
  }
  * { margin: 0; padding: 0; box-sizing: border-box; }
  html, body { width: 800px; height: 1200px; overflow: hidden; background: var(--paper); }
  body { font-family: "Montserrat", Arial, sans-serif; color: var(--ink); }
  .sheet { position: relative; width: 800px; height: 1200px; background: var(--paper); overflow: hidden; }

  .brand { position: absolute; left: 44px; top: 72px; display: flex; align-items: center; gap: 12px; }
  .brand-square { width: 34px; height: 34px; background: var(--navy); }
  .brand-name { font-size: 31px; font-weight: 700; color: var(--navy); letter-spacing: 0.2px; }

  .title-band {
    position: absolute; left: 0; top: 177px; width: 371px; height: 283px;
    background: linear-gradient(180deg, #2fb0cb 0%, #237f93 55%, var(--teal-dark) 100%);
  }
  .title { position: absolute; left: 46px; top: 30px; color: #fff; font-weight: 800; font-size: 68px; line-height: 66px; letter-spacing: 1px; }
  .title-rule { position: absolute; left: 46px; top: 186px; width: 300px; height: 2px; background: #e6f3f6; }
  .title-rule::before { content: ""; position: absolute; left: 20px; top: -1px; width: 42px; height: 4px; background: var(--navy); }
  .subtitle { position: absolute; left: 46px; top: 218px; color: #fff; font-size: 14.5px; line-height: 18px; font-weight: 500; }

  .hero { position: absolute; left: 360px; top: 30px; width: 440px; height: 600px; }

  .section-title { font-weight: 700; font-size: 24px; color: var(--teal); letter-spacing: 0.5px; }
  .section-rule { position: relative; height: 1px; background: var(--rule); margin-top: 12px; }
  .section-rule::before { content: ""; position: absolute; left: 0; top: -1px; width: 28px; height: 3px; background: var(--navy); }

  .strategy { position: absolute; left: 44px; top: 505px; width: 330px; }
  .strategy .section-rule { width: 168px; }
  .strategy p { margin-top: 30px; font-size: 12.6px; line-height: 16.4px; text-align: justify; color: var(--ink); }

  .pool-photo {
    position: absolute; left: 44px; top: 807px; width: 329px; height: 274px;
    border: 3px solid #fff; box-shadow: 0 1px 4px rgba(0,0,0,0.25);
    background: linear-gradient(160deg, #1f7fa8 0%, #38b6dc 40%, #7fd6ee 70%, #2a9bc4 100%);
  }

  .workflow { position: absolute; left: 423px; top: 632px; width: 350px; }
  .workflow .section-title { color: var(--ink); font-weight: 500; }
  .workflow .section-title span { color: var(--teal); font-weight: 700; }
  .workflow .section-rule { background: transparent; }
  .steps { list-style: none; position: absolute; left: 0; top: 56px; width: 350px; }
  .steps li { position: absolute; left: 0; width: 345px; padding-left: 31px; font-size: 13px; line-height: 16.3px; color: var(--ink); }
  .steps li::before { content: ""; position: absolute; left: 2px; top: 3px; width: 9px; height: 9px; border: 2px solid var(--navy); border-radius: 50%; }

  .footer-band { position: absolute; left: 0; top: 1115px; width: 800px; height: 85px; }
  .phone { position: absolute; left: 44px; top: 1130px; color: #fff; font-weight: 700; font-size: 21px; display: flex; align-items: center; gap: 8px; }
  .address { position: absolute; left: 44px; top: 1166px; color: #fff; font-size: 13.5px; display: flex; align-items: center; gap: 9px; }
  .contact { position: absolute; left: 464px; top: 1145px; font-size: 15px; color: var(--ink); display: flex; align-items: center; gap: 7px; }
  .contact svg { flex: none; }
</style>
</head>
<body>
<main class="sheet">

  <header class="brand">
    <span class="brand-square"></span>
    <span class="brand-name">VORLE Diagnostics</span>
  </header>

  <section class="title-band">
    <h1 class="title">POOLED<br>TESTING</h1>
    <div class="title-rule"></div>
    <p class="subtitle">POOLED SAMPLE TESTING AND<br>SCREENING TESTING FOR COVID-19</p>
  </section>

  <svg class="hero" viewBox="360 30 440 600" xmlns="http://www.w3.org/2000/svg">
    <defs>
      <linearGradient id="heroTone" x1="0" y1="0" x2="1" y2="1">
        <stop offset="0" stop-color="#eef3ee"/>
        <stop offset="0.35" stop-color="#b9cfa2"/>
        <stop offset="0.7" stop-color="#d9dee2"/>
        <stop offset="1" stop-color="#8d9aa6"/>
      </linearGradient>
    </defs>
    <polyline points="742,170 360,392 360,395" fill="none" stroke="var(--navy)" stroke-width="0"/>
    <path d="M372,440 L372,208 L570,98" fill="none" stroke="#2b4352" stroke-width="9"/>
    <path d="M738,64 L800,99" fill="none" stroke="#2b4352" stroke-width="9"/>
    <path d="M381,500 L372,505" fill="none" stroke="#2b4352" stroke-width="0"/>
    <path d="M372,470 L372,498 L606,630" fill="none" stroke="#2b4352" stroke-width="0"/>
    <path d="M740,585 L800,551" fill="none" stroke="#2b4352" stroke-width="9"/>
    <path d="M390,518 L318,560" fill="none" stroke="#2b4352" stroke-width="7"/>
    <path d="M300,168 L380,212" fill="none" stroke="#2b4352" stroke-width="7"/>
    <polygon points="397,189 606,67 814,189 814,466 606,588 397,466" fill="none" stroke="#2b4352" stroke-width="10"/>
    <polygon role="img" aria-label="Photo: a health worker in protective suit and mask takes a throat swab from a young woman" points="397,189 606,67 814,189 814,466 606,588 397,466" fill="url(#heroTone)"/>
  </svg>

  <section class="strategy">
    <h2 class="section-title">STRATEGY</h2>
    <div class="section-rule"></div>
    <p>The process and concept for pooling is to target large populations of people; i.e. a school, prison, employer (where people are isolated by pods), then to test them all in one controllable group. By breaking down the pool size (ideally is 12 or 16 max) then when a positive pool pops up, the entity has the lab automatically reflex to test the whole pool to determine who is positive. During that exchange, several workflows could take place from the population that was being tested. This type of pooled testing is called Surveillance testing, when it reflects, then it goes to Screening or Diagnostic testing.</p>
  </section>

  <div class="pool-photo" role="img" aria-label="Photo: a hand holds a water test kit with coloured vials above a blue swimming pool"></div>

  <section class="workflow">
    <h2 class="section-title">THE <span>WORKFLOW IS:</span></h2>
    <div class="section-rule"></div>
    <ul class="steps">
      <li style="top:0">School/employer collects all patient information captured on a requisition form or electronically (w signature) and DOES NOT send to VORLE</li>
      <li style="top:66px">School/employer collects individual specimens and labels them with a unique bar code (non-repeating and can include the DOB)</li>
      <li style="top:130px">School/employer is responsible for housing and managing all the unique patient information for each individual specimen</li>
      <li style="top:194px">School/employer delivers specimens to VORLE and School/employer directs VORLE what specimens are in what designated pool (one pool size for entire project)</li>
      <li style="top:271px">When a pool is positive, VORLE notifies School/employer</li>
      <li style="top:321px">When reflex testing in indicated for client, School/employer submits to VORLE on demand all patient information needed to process the reflexed option</li>
      <li style="top:402px">VORLE reports back to School/employer in 12 hours the results of the retest</li>
    </ul>
  </section>

  <svg class="footer-band" viewBox="0 1115 800 85" xmlns="http://www.w3.org/2000/svg">
    <polygon points="0,1115 412,1115 475,1200 0,1200" fill="#2b4352"/>
    <rect x="475" y="1180" width="325" height="7" fill="#34a6d7"/>
  </svg>

  <div class="phone">
    <svg width="15" height="15" viewBox="0 0 24 24"><path d="M6.6 10.8a15.1 15.1 0 0 0 6.6 6.6l2.2-2.2a1 1 0 0 1 1-.25 11.4 11.4 0 0 0 3.6.57 1 1 0 0 1 1 1V20a1 1 0 0 1-1 1A17 17 0 0 1 3 4a1 1 0 0 1 1-1h3.5a1 1 0 0 1 1 1c0 1.25.2 2.45.57 3.57a1 1 0 0 1-.25 1z" fill="#34a6d7"/></svg>
    844-555-0193
  </div>
  <div class="address">
    <svg width="11" height="15" viewBox="0 0 12 16"><path d="M6 0a6 6 0 0 0-6 6c0 4.5 6 10 6 10s6-5.5 6-10a6 6 0 0 0-6-6zm0 8.2A2.2 2.2 0 1 1 6 3.8a2.2 2.2 0 0 1 0 4.4z" fill="#34a6d7"/></svg>
    1280 Harbor Point Drive Suite 4 Lakeview, MD 21990
  </div>
  <div class="contact">
    <svg width="14" height="10" viewBox="0 0 14 10"><rect x="0.5" y="0.5" width="13" height="9" fill="none" stroke="#2e9fb8"/><path d="M0.5 0.5 L7 5.5 L13.5 0.5" fill="none" stroke="#2e9fb8"/></svg>
    <span>info@vorledx.com</span>
    <svg width="12" height="12" viewBox="0 0 12 12" style="margin-left:6px"><circle cx="6" cy="6" r="5.3" fill="none" stroke="#2e9fb8" stroke-width="1.2"/><ellipse cx="6" cy="6" rx="2.3" ry="5.3" fill="none" stroke="#2e9fb8"/><path d="M0.7 6 H11.3" stroke="#2e9fb8"/></svg>
    <span>www.vorledx.com</span>
  </div>

</main>
</body>
</html>
```